tallow-brook.com

We are a small dollar lending company that will revolutionize the industry. We will do this by being completely transparent, fee free, etc and an interest rate that normal people can afford to pay. Over 10X less than our competition. We only allow our members to pay bills " bills paid fast", within 72 hours. Payday loans typically charge from 390%-600% with a terrible payback structure. We charge 36%, period, with a payback structure over 12 months. Our site will be very simple and easy to use but elegant at the same time. We do not want the site to be too busy, less is more and easier. We will have; Home, The Story, Why tallowbrook.com, Are you eligible? Members, Clients. To become a member you have to be referred by a current client of tallowbrook.com. A lot of the busy stuff will be saved for the Members and Clients sections. The feel must be elegant, easy to use and very simple to understand. I am looking for the green, white and black combinations of colors, very similar to my logo that was designed by Fernquillo.

```html
<!DOCTYPE html>
<html lang="en">
<head>
<meta charset="utf-8">
<title>Tallow Brook — Small Dollar Lending</title>
<link href="https://fonts.googleapis.com/css2?family=Open+Sans:wght@400;600&family=PT+Sans:wght@400;700&display=swap" rel="stylesheet">
<style>
:root{
  --green:#6fa82a;
  --green-light:#8cc63f;
  --green-dark:#5f9a22;
  --ink:#333;
  --grey-text:#777;
  --nav:#8a8a8a;
  --footer-bg:#eeeeee;
  --card-bg:#f4f4f4;
  --blue:#3f6fd0;
  --white:#fff;
}
*{margin:0;padding:0;box-sizing:border-box}
html,body{width:960px;height:1200px;overflow:hidden;background:var(--white)}
body{position:relative;font-family:"Open Sans",Arial,sans-serif;color:var(--ink)}
.abs{position:absolute}

/* header */
.brand{left:64px;top:18px;display:flex;align-items:center;gap:8px;font-family:"Open Sans",sans-serif;font-size:19px;font-weight:600;color:var(--ink)}
.brand-dot{width:28px;height:28px;border-radius:50%;background:var(--green-light)}
.nav{left:314px;top:26px;display:flex;align-items:center;font-size:12px;color:var(--nav)}
.nav a{color:inherit;text-decoration:none;margin-right:26px}
.nav .active{border:1px solid var(--green);color:var(--green);border-radius:13px;padding:3px 12px;margin-right:14px;font-weight:600}
.login{left:810px;top:26px;width:71px;height:23px;background:var(--green);color:var(--white);font-size:11px;font-weight:600;display:flex;align-items:center;justify-content:center}

/* slider */
.hero{left:0;top:77px;width:960px;height:401px;background:radial-gradient(ellipse at 60% 45%,#5b8ee6 0%,#3a67c8 55%,#2c55b4 100%)}
.hero-photo{left:110px;top:18px;width:260px;height:383px;background:linear-gradient(160deg,#e8ece8 0%,#c9d3c9 60%,#6d4a33 100%);opacity:.9}
.hero-arrow{width:29px;height:29px;border:1.5px solid var(--white);border-radius:50%;top:183px}
.hero-panel{left:660px;top:57px;width:220px;height:291px;background:rgba(205,218,240,.92);text-align:center;padding-top:22px}
.hero-panel h2{font-weight:400;font-size:19px;color:#222}
.hero-panel p.lead{font-size:10.5px;color:#555;margin:12px 16px 0;line-height:15px}
.hero-panel .hl{color:var(--green);font-weight:600}
.stat{position:absolute;left:19px;width:182px;background:rgba(235,241,250,.9);padding:5px 10px}
.stat b{display:block;color:var(--green-light);font-size:14px}
.stat span{font-size:9.5px;color:#333;line-height:14px;display:block}
.dots{top:486px;left:458px;display:flex;gap:6px}
.dots i{width:8px;height:8px;border-radius:50%;border:1px solid #aaa}
.dots i.on{background:var(--green-light);border-color:var(--green-light)}

/* welcome */
.welcome-title{left:81px;top:543px;font-family:"PT Sans",sans-serif;font-weight:700;font-size:15px;letter-spacing:.5px;color:#333}
.welcome-photo{left:81px;top:580px;width:184px;height:157px;background:linear-gradient(135deg,#d9dde0,#a6adb3)}
.simple-title{left:282px;top:590px;font-family:"PT Sans",sans-serif;font-size:16px;color:#444}
.copy{font-family:Arial,sans-serif;font-size:10.4px;line-height:14.4px;color:var(--grey-text);text-align:justify}
.copy-main{left:282px;top:624px;width:317px}
.copy-end{left:80px;top:752px;width:520px;text-align:left}
.promise{left:627px;top:546px;width:254px;height:231px;background:linear-gradient(180deg,var(--green-light),var(--green-dark));box-shadow:2px 2px 3px rgba(0,0,0,.25);color:var(--white);text-align:center;font-size:14px;line-height:20px;letter-spacing:.5px;padding-top:20px}
.promise .lead{font-size:19px;margin:10px 0 4px}

/* action cards */
.card{top:836px;width:252px;height:82px;background:var(--card-bg);box-shadow:0 1px 3px rgba(0,0,0,.15);text-align:center;padding-top:22px}
.card h3{font-weight:400;font-size:19px;color:var(--green-light);letter-spacing:.3px}
.card p{font-size:9.5px;color:#666}
.card.primary{background:var(--green);box-shadow:none}
.card.primary h3,.card.primary p{color:var(--white)}

/* footer */
.footer{left:0;top:971px;width:960px;height:182px;background:linear-gradient(180deg,#ededed,#f7f7f7)}
.col{top:1005px;font-size:9.5px;color:#333}
.col h4{font-weight:400;font-size:11.5px;margin-bottom:13px}
.col li{list-style:none;margin-bottom:9px}
.news{display:flex;gap:10px;margin-bottom:14px}
.news-thumb{width:33px;height:36px}
.news b{font-weight:600;font-size:10px;display:block}
.news span{font-size:8.5px;color:#666;display:block;line-height:13px}
.social{display:flex;align-items:center;gap:12px;font-size:11px;color:#555;margin-bottom:18px}
.social i{width:16px;height:16px;border-radius:50%;background:#999}
.bar{left:0;top:1153px;width:960px;height:47px;background:var(--green);color:var(--white);font-size:9.5px;text-align:center;line-height:47px}
</style>
</head>
<body>

<header>
  <div class="abs brand"><span class="brand-dot"></span>Tallow Brook</div>
  <nav class="abs nav">
    <a class="active" href="#">Home</a><a href="#">The Story</a><a href="#">Why tallowbrook.com</a><a href="#">Are you eligible?</a><a href="#">Members</a><a href="#">Clients</a>
  </nav>
  <a class="abs login">LOGIN</a>
</header>

<section class="abs hero">
  <div class="abs hero-photo" role="img" aria-label="Hand holding a fan of banknotes"></div>
  <svg class="abs hero-arrow" style="left:28px" viewBox="0 0 29 29"><path d="M16 9 L11 14.5 L16 20" fill="none" stroke="#fff" stroke-width="1.5"/></svg>
  <svg class="abs hero-arrow" style="left:905px" viewBox="0 0 29 29"><path d="M13 9 L18 14.5 L13 20" fill="none" stroke="#fff" stroke-width="1.5"/></svg>
  <div class="abs hero-panel">
    <h2>TALLOW BROOK</h2>
    <p class="lead">We will do Money Lending by being completely <span class="hl">transparent</span>, <span class="hl">fee free</span></p>
    <div class="stat" style="top:129px"><b>%</b><span>interest rate that normal people can afford to pay</span></div>
    <div class="stat" style="top:202px"><b>10x</b><span>Over 10X less than our competition</span></div>
  </div>
</section>
<div class="abs dots"><i class="on"></i><i></i><i></i></div>

<main>
  <h1 class="abs welcome-title">WELCOME TO OUR SITE</h1>
  <div class="abs welcome-photo" role="img" aria-label="Smiling businessman in an office"></div>
  <h2 class="abs simple-title">It's Simple</h2>
  <p class="abs copy copy-main">Small dollar loans are either too hard to get, take too long to process or just impossible to pay back. There are between 15mm-18mm people each year that require the use of small dollar loans, so you are not alone. Let's face it we are all short on cash at some point. At tallow-brook.com we have created a product that is very accessible, has a quick turnaround and best of all the payback terms are very reasonable. We will never charge you a late fee, app fee, transaction fee or anything that resembles a fee.</p>
  <p class="abs copy copy-end">Sorry, if you bounce a check we will charge you the bounce check fee, there are some things even we can't overlook.</p>

  <aside class="abs promise">
    <svg width="50" height="50" viewBox="0 0 50 50"><circle cx="25" cy="25" r="22" fill="none" stroke="#fff" stroke-width="4" stroke-dasharray="6 2"/><circle cx="25" cy="25" r="13" fill="none" stroke="#fff" stroke-width="3"/><path d="M19 25 L23.5 29.5 L31 21" fill="none" stroke="#fff" stroke-width="3.5"/></svg>
    <div class="lead">We charge only 36%</div>
    and<br>Give over 12 months time<br>to pay back,<br>No fees, Hidden costs<br>etc...
  </aside>

  <a class="abs card primary" style="left:81px"><h3>CALCULATE</h3><p>How Much Do I Have to Payback</p></a>
  <a class="abs card" style="left:353px"><h3>ARE YOU ELIGIBLE</h3><p>You Must be Referred</p></a>
  <a class="abs card" style="left:627px"><h3>PAY BILLS</h3><p>Bills Paid Fast</p></a>
</main>

<footer>
  <div class="abs footer"></div>
  <div class="abs col" style="left:81px"><h4>Need help?</h4><ul><li>Our Services</li><li>Timesheets</li><li>FAQ</li><li>Terms and Conditions</li></ul></div>
  <div class="abs col" style="left:255px"><h4>User area</h4><ul><li>Our Services</li><li>FAQ</li><li>Terms and Conditions</li></ul></div>
  <div class="abs col" style="left:415px"><h4>Latest News</h4>
    <div class="news"><div class="news-thumb" role="img" aria-label="Blue data screen thumbnail" style="background:linear-gradient(135deg,#1b3fa0,#5f86d8)"></div><div><b>Lorem ipsum</b><span>simply dummy text of the printing and typesetting</span><span>Feb - 14 - 2014</span></div></div>
    <div class="news"><div class="news-thumb" role="img" aria-label="Pen signing a document thumbnail" style="background:linear-gradient(135deg,#f1eeea,#b9a89a)"></div><div><b>Dolor sit ipsum</b><span>simply dummy text of the printing and typesetting</span><span>Feb - 14 - 2014</span></div></div>
  </div>
  <div class="abs col" style="left:730px"><h4>Get In Touch</h4>
    <div class="social" style="margin-top:22px"><i></i>Netweave</div>
    <div class="social"><i></i>Chirpline</div>
  </div>
  <div class="abs bar">Copyright yoursite.com | Site Map | Contact Details | Privacy Policy</div>
</footer>

</body>
</html>
```